KVB Website

We need a website for a company based in Doha Qatar called Brightpath Talent Global. It is a global recruitment company, that specializes in both mass recruitment and headhunting. The company is the number 1 one stop shop for recruitment in Qatar. It recruits from all over the world Europe, Asia, Americas, Middle East, Africa for Qatar.

Target Market(s)

Multinational companies, fortune 500 company CEO's, any top earning companies that are looking for a large number of employees or headhunting employees.
Also for candidates looking for companies to work in Qatar.

Industry/Entity Type

Shop

Colors
ffffff

Requirements
Must have
• Most important qualities the website needs to have:
Clean
Modern
Elegant
Professional
Less Tabs
Minimalisitc

Some examples, I would like you to follow are here:
http://www.velmora.ca/
http://www.trovenkip.com/
https://quelbrandix.com/match#

The main color should be white and it has to have a very stylish, modern and cool look. While being minimalistic. I do not want too many tabs. I want it to be simplistic to understand. the only place where the pink logo color is should be in the logo. The logo color should not be anywhere else. It has to be absolutely sleek. Please follow the example websites that I have provided.

I will send the contact details you need to add later. There is no need for a log in page.

Whatever you think that may be important for a recruitment site do suggest. But there is no need for a log in area as we are a different kind of recruitment company.

There should be an area for testimonials from clients. There should also be an area for news flash for the latest countries we are hiring from and the latest companies we are hiring for and the latest positions we are looking for.

Show me the best please. Whoever gives me the best, I will give them an order for the 2nd website too.

Nice to have
• I have included a powerpoint to explain more!

```html
<!DOCTYPE html>
<html lang="en">
<head>
<meta charset="utf-8">
<title>Brightpath Talent Global</title>
<link href="https://fonts.googleapis.com/css2?family=Open+Sans:ital,wght@0,400;0,600;0,700;1,600&display=swap" rel="stylesheet">
<style>
:root{
  --logo:#a5195e;
  --accent:#3a3a3a;
  --ink:#333;
  --text:#555;
  --muted:#888;
  --panel:#3a3a3a;
  --light:#f3f3f3;
  --band:#ececec;
  --footer:#3b3b3b;
  --footer-text:#9a9a9a;
  --white:#fff;
}
*{box-sizing:border-box;margin:0;padding:0}
html,body{width:682px;height:1200px;overflow:hidden}
body{font-family:"Open Sans",sans-serif;color:var(--text);background:var(--white);font-size:8px;position:relative}
.wrap{width:534px;margin-left:74px;position:relative;height:100%}

/* header */
.site-header{height:98px}
.brand{position:absolute;left:0;top:6px}
.brand-mark{width:34px;height:34px;border-radius:50%;background:var(--logo);margin-left:10px}
.brand-name{font-weight:700;color:var(--logo);font-size:8px;line-height:9px;margin-top:7px}
.brand-sub{font-weight:700;color:var(--logo);font-size:5px;margin-left:6px}
.tagline{position:absolute;left:0;top:78px;font-size:7px;color:#666}
.top-links{position:absolute;right:0;top:13px;font-size:7px;color:#666;word-spacing:2px}
.top-links span{color:#aaa;margin:0 4px}
.call{position:absolute;left:302px;top:57px;display:flex;align-items:center;gap:6px}
.call svg{width:13px;height:13px}
.call-label{color:var(--ink);font-weight:600;font-size:8px;line-height:8px}
.call-num{font-size:13px;color:#222;line-height:14px}
.search{position:absolute;right:0;top:59px;width:125px;height:21px;border:1px solid #ccc;border-radius:2px;background:linear-gradient(#f4f4f4,#fff)}
.search svg{position:absolute;right:5px;top:5px;width:11px;height:11px}

/* nav */
.main-nav{height:27px;background:linear-gradient(#4a4a4a,#333)}
.main-nav ul{list-style:none;display:flex;height:27px;align-items:center;margin-left:74px}
.main-nav li{color:#fff;font-size:7px;font-weight:600;margin-right:29px}

/* hero */
.hero{height:248px;background:var(--band)}
.slider{position:absolute;top:7px;left:0;width:534px;height:226px;border:3px solid #fff;background:linear-gradient(135deg,#c9ccd0,#8b8f96 40%,#5a5f68 70%,#b7bbc1)}
.caption{position:absolute;left:0;top:84px;width:315px;height:53px;background:rgba(40,40,40,.72);color:#fff;font-size:14px;line-height:18px;padding:8px 13px}
.dots{position:absolute;left:14px;bottom:14px;display:flex;gap:3px}
.dots i{width:9px;height:9px;background:#eee;border-radius:1px}

/* welcome */
.welcome{height:248px}
.welcome h1{position:absolute;top:23px;left:0;font-weight:400;font-size:14px;color:var(--ink)}
.welcome .copy{position:absolute;top:47px;left:0;width:342px;font-size:7px;line-height:13px}
.welcome .copy p{margin-bottom:4px}
.btn{display:inline-block;background:var(--accent);color:#fff;font-weight:700;font-size:6.5px;padding:7px 13px}
.welcome .btn{position:absolute;top:212px;left:0;width:67px;height:21px}
.mission{position:absolute;right:0;top:26px;width:170px;height:206px;background:var(--panel);color:#fff;text-align:center;padding-top:11px}
.mission h2{font-weight:400;font-size:10px;line-height:14px}
.mission h2 b{font-weight:600;font-size:12px}
.mission-photo{width:151px;height:81px;margin:8px auto 10px;background:linear-gradient(180deg,#c7ccd1,#7c838c)}
.mission p{font-size:7px;line-height:9.5px;padding:0 14px;margin-bottom:4px}

/* clients */
.clients{height:163px;background:var(--light)}
.clients h2{text-align:center;font-weight:400;color:var(--ink);font-size:13px;padding-top:11px}
.logo-row{display:flex;gap:3px;position:absolute}
.logo-row.r1{top:42px;left:0}
.logo-row.r2{top:89px;left:41px}
.logo{height:38px;border:1px solid #aaa;background:#fff;display:flex;align-items:center;justify-content:center;gap:4px;font-size:8px;font-weight:600;color:#444}
.logo i{width:8px;height:8px;border-radius:50%;background:#999}
.arrows{position:absolute;top:138px;left:252px;display:flex;gap:4px}
.arrows svg{width:12px;height:12px}

/* services */
.services{height:238px}
.card{position:absolute;top:19px;height:202px;background:var(--light)}
.card h2{font-weight:400;font-size:13px;color:var(--ink)}
.card-services{left:0;width:171px;padding:12px 13px}
.card-services p{font-size:7px;line-height:13px;margin-top:6px}
.card-services .btn{margin-top:15px;width:67px;height:20px}
.card-procedure{left:182px;width:352px;padding:12px 11px}
.proc-photo{position:absolute;left:11px;top:37px;width:129px;height:138px;background:linear-gradient(160deg,#9ea4ab,#4d535b 60%,#d3d6da)}
.steps{position:absolute;left:152px;top:35px;width:195px}
.steps .lead{font-style:italic;font-weight:600;font-size:7px;line-height:10px;color:#555;margin-bottom:8px}
.step{display:flex;gap:9px;align-items:flex-start;margin-bottom:9px;font-size:7px;line-height:11px;min-height:22px}
.step b{flex:none;width:19px;height:19px;border-radius:50%;background:var(--accent);color:#fff;font-size:7px;display:flex;align-items:center;justify-content:center}
.step span{padding-top:2px}

/* footer */
.site-footer{height:178px;background:var(--footer);color:var(--footer-text)}
.site-footer h3{color:#fff;font-size:8px;font-weight:600;margin-bottom:5px}
.f-col{position:absolute;top:15px;font-size:6.5px;line-height:14px}
.f-news{left:0;width:195px;line-height:11px}
.f-news strong{display:block;color:#fff;font-size:6.5px;margin-top:6px}
.rule{position:absolute;top:113px;left:0;width:534px;border-top:1px solid #555}
.copyright{position:absolute;left:0;top:134px;font-size:6.5px;line-height:11px}
.copyright b{color:#fff;font-weight:400}
.follow{position:absolute;right:0;top:124px;width:90px}
.follow h3{margin-left:6px}
.social{display:flex;gap:3px;margin-top:5px}
.social span{display:flex;align-items:center;gap:2px;font-size:6px;color:#ddd}
.social i{width:8px;height:8px;background:#777}
</style>
</head>
<body>

<header class="site-header">
  <div class="wrap">
    <div class="brand">
      <div class="brand-mark"></div>
      <div class="brand-name">BRIGHTPATH</div>
      <div class="brand-sub">TALENT GLOBAL</div>
    </div>
    <div class="tagline">Qatar's leading One-Stop-Shop for Global Recruitment</div>
    <div class="top-links">FAQ<span>|</span>SITE MAP</div>
    <div class="call">
      <svg viewBox="0 0 13 13"><rect width="13" height="13" rx="2" fill="#3a3a3a"/><path d="M4 3c1 0 1.4 1.5 1 2l-.6.6c.5 1 1.2 1.7 2 2l.6-.6c.5-.4 2 0 2 1 0 1-1 1.5-1.6 1.3C5 8.7 3.9 7.5 3 5.2 2.8 4 3.2 3 4 3z" fill="#fff"/></svg>
      <div><div class="call-label">Call:</div><div class="call-num">100 555 0199</div></div>
    </div>
    <div class="search"><svg viewBox="0 0 11 11"><circle cx="4.5" cy="4.5" r="3.2" fill="none" stroke="#222" stroke-width="1.4"/><path d="M7 7l3.3 3.3" stroke="#222" stroke-width="1.8"/></svg></div>
  </div>
</header>

<nav class="main-nav">
  <ul><li>HOME</li><li>ABOUT US</li><li>SERVICES</li><li>CLIENTS</li><li>LATEST NEWS</li><li>TESTIMONIALS</li><li>BLOG</li><li>CONTACT US</li></ul>
</nav>

<section class="hero">
  <div class="wrap">
    <div class="slider" role="img" aria-label="Business people shaking hands across a meeting table">
      <div class="caption">Strive to be the best at helping employers achieve success through people.</div>
      <div class="dots"><i></i><i></i><i></i><i></i></div>
    </div>
  </div>
</section>

<section class="welcome">
  <div class="wrap">
    <h1>Welcome to Brightpath Talent Global (KVB)</h1>
    <div class="copy">
      <p>Brightpath Talent Global, popularly known as KVB, established in Doha, State of Qatar, is one of the pioneers of local and overseas recruitment along with manpower placements. It is our credibility and expertise in the business as proven by our experience and clients' success, which makes us able and fully equipped to understand both the employer's/employee's needs and meet them with skill, commitment and efficiency.</p>
      <p>We fulfill the needs of our clients by matching the industry's most talented professionals from different parts of the world with companies who need their assistance. We are able to cater for a wide variety of requirements, from front line staff right up to senior level management. Brightpath Talent Global is comprised of experienced professionals from a range of backgrounds, including business and financial services and consultancy, human resources, the service sector and the hospitality sector, in the Middle East, Asia and Europe.</p>
    </div>
    <span class="btn">READ MORE</span>
    <aside class="mission">
      <h2>Brightpath Talent Global<br><b>Mission Statement</b></h2>
      <div class="mission-photo" role="img" aria-label="Three businessmen standing in front of office towers"></div>
      <p>Our mission statement guides our future strategy.</p>
      <p>Our mission is to be the best at helping employers achieve success through people.</p>
    </aside>
  </div>
</section>

<section class="clients">
  <div class="wrap">
    <h2>Our Clients</h2>
    <div class="logo-row r1">
      <div class="logo" style="width:78px"><i></i>Nakhla Dates</div>
      <div class="logo" style="width:93px"><i></i>Zarwan Group</div>
      <div class="logo" style="width:119px">Falcona Air</div>
      <div class="logo" style="width:102px">Grand Meridel</div>
      <div class="logo" style="width:128px">Rahla Transit</div>
    </div>
    <div class="logo-row r2">
      <div class="logo" style="width:122px">Dunecourt Hotels</div>
      <div class="logo" style="width:142px"><i></i>Harborline Engineering</div>
      <div class="logo" style="width:98px"><i></i>Hydravon</div>
      <div class="logo" style="width:77px">Tableway Foods</div>
    </div>
    <div class="arrows">
      <svg viewBox="0 0 12 12"><circle cx="6" cy="6" r="5.5" fill="#eee" stroke="#999"/><path d="M7.5 3.5v5L4 6z" fill="#222"/></svg>
      <svg viewBox="0 0 12 12"><circle cx="6" cy="6" r="5.5" fill="#eee" stroke="#999"/><path d="M4.5 3.5v5L8 6z" fill="#222"/></svg>
    </div>
  </div>
</section>

<section class="services">
  <div class="wrap">
    <div class="card card-services">
      <h2>KVB Services</h2>
      <p>We are confident to recruit for wide range of industries starting from organizing mass recruitment campaign for lower positions that could range in thousands of candidates in one go or head hunting of a specialist for senior level positions from a specific country. Our experience has been the key source of our confidence.</p>
      <span class="btn">READ MORE</span>
    </div>
    <div class="card card-procedure">
      <h2>KVB Recruitment Procedure</h2>
      <div class="proc-photo" role="img" aria-label="Colleagues reviewing work on a laptop"></div>
      <div class="steps">
        <p class="lead">Steps we follow in order to recruit for you from the overseas market..</p>
        <div class="step"><b>1</b><span>Confirm the business deal with employer company..</span></div>
        <div class="step"><b>2</b><span>Job order confirmation.</span></div>
        <div class="step"><b>3</b><span>Coordinate further procedures with employer HR until selected candidates join.</span></div>
        <div class="step"><b>4</b><span>Confirm the flight schedule and deploy the worker.</span></div>
      </div>
    </div>
  </div>
</section>

<footer class="site-footer">
  <div class="wrap">
    <div class="f-col f-news">
      <h3>Update New</h3>
      Nunc consequat congue nulla eu imperdiet. Donec in est erat, id malesuada turpis. Nunc a dui id turpis convallis semper vitae eros placerat..
      <strong>Posted on Mar25, 2014</strong>
    </div>
    <div class="f-col" style="left:231px"><h3>Footer Links</h3>Aenean a nibh eget<br>Turpis vehicula tempus<br>Ac sed massa<br>Vestibulum dolor<br>Lorem euismod</div>
    <div class="f-col" style="left:343px"><h3>Footer Links</h3>Aenean a nibh eget<br>Turpis vehicula tempus<br>Ac sed massa<br>Vestibulum dolor<br>Lorem euismod</div>
    <div class="f-col" style="left:451px"><h3>Footer Links</h3>Aenean a nibh eget<br>Turpis vehicula tempus<br>Ac sed massa<br>Vestibulum dolor<br>Lorem euismod</div>
    <div class="rule"></div>
    <div class="copyright">Copyright © 2014. <b>BRIGHTPATH TALENT GLOBAL.</b><br>All Right Reserved</div>
    <div class="follow">
      <h3>Follow Us:</h3>
      <div class="social"><span><i></i>Folio</span><span><i></i>Chirpa</span><span><i></i>Netwrk</span><span><i></i>Feed</span></div>
    </div>
  </div>
</footer>

</body>
</html>
```